Brindle Yard Care. The best in the biz

I run a lawn care service that offers full service mowing. 100% satisfaction guarantee. Fast, Friendly, quality service "I am your lawns best friend" I cut residential lawns. I offer a mow package that includes trimming, edging and clean up. Prices very from 20 dollars to 75. I want my logo to stand out. Free estimates

Target Market(s)

Home owners

Industry/Entity Type

Landscaping

Contact Information for Business Card

555-812-4473 tomvale48@quillmail.net Derek. Brindle Yard care

Colors
f37122
9bcb3c
cadf82

Requirements
Must have
• Company name.
• Phone number
• Email
• My services
• images
Nice to have
• A sun that is growing grass.
Should not have
• Incorrect information

```html
<!DOCTYPE html>
<html lang="en">
<head>
<meta charset="utf-8">
<title>Brindle Yard Care – Business Card</title>
<link href="https://fonts.googleapis.com/css2?family=Arimo:wght@400;700&display=swap" rel="stylesheet">
<style>
  :root {
    --page-bg: #e9e6df;
    --card-white: #ffffff;
    --lawn-green: #9bcb3c;
    --lawn-green-light: #b9dc5a;
    --pale-green: #cadf82;
    --brand-green: #1f9a4a;
    --sun-yellow: #f5c21d;
    --ink: #1b1b1b;
    --swoosh: #141a14;
  }
  html, body {
    margin: 0;
    padding: 0;
    width: 1200px;
    height: 780px;
    overflow: hidden;
    background: var(--page-bg);
    font-family: "Arimo", Arial, sans-serif;
  }
  .canvas {
    position: relative;
    width: 1200px;
    height: 780px;
    display: flex;
    align-items: center;
    justify-content: center;
  }
  .business-card {
    position: relative;
    width: 1050px;
    height: 600px;
    background: var(--card-white);
    box-shadow: 0 10px 30px rgba(0,0,0,0.18);
    overflow: hidden;
  }
  .card-shapes {
    position: absolute;
    inset: 0;
  }
  .brand-block {
    position: absolute;
    left: 70px;
    top: 225px;
    width: 540px;
  }
  .brand-row {
    display: flex;
    align-items: center;
    gap: 18px;
  }
  .brand-dot {
    width: 70px;
    height: 70px;
    border-radius: 50%;
    background: var(--sun-yellow);
    flex: none;
  }
  .brand-name {
    margin: 0;
    font-size: 46px;
    line-height: 1.1;
    font-weight: 400;
    color: var(--brand-green);
    white-space: nowrap;
  }
  .tagline {
    margin: 30px 0 0 88px;
    font-size: 27px;
    color: var(--ink);
    font-weight: 400;
  }
  .contact-block {
    position: absolute;
    left: 720px;
    top: 130px;
    width: 310px;
    color: var(--ink);
  }
  .contact-name {
    margin: 0;
    font-size: 38px;
    font-weight: 700;
  }
  .contact-company {
    margin: 8px 0 20px;
    font-size: 23px;
  }
  .contact-line {
    display: flex;
    align-items: center;
    gap: 10px;
    margin: 0 0 12px;
    font-size: 22px;
  }
  .contact-icon {
    width: 26px;
    height: 26px;
    flex: none;
  }
  .promise {
    margin: 0 0 8px;
    font-size: 22px;
  }
  .promise:first-of-type { margin-top: 20px; }
  .services {
    margin: 14px 0 0;
    font-size: 19px;
    line-height: 1.35;
  }
</style>
</head>
<body>
<main class="canvas">
  <section class="business-card">
    <svg class="card-shapes" width="1050" height="600" viewBox="0 0 1050 600" aria-hidden="true">
      <defs>
        <linearGradient id="lawnFill" x1="0" y1="0" x2="1" y2="1">
          <stop offset="0" stop-color="#b9dc5a"/>
          <stop offset="1" stop-color="#9bcb3c"/>
        </linearGradient>
        <linearGradient id="whiteFill" x1="0" y1="0" x2="1" y2="0">
          <stop offset="0" stop-color="#ffffff"/>
          <stop offset="1" stop-color="#f1f1f1"/>
        </linearGradient>
      </defs>
      <rect width="1050" height="600" fill="url(#whiteFill)"/>
      <path class="swoosh" d="M560 0 Q745 300 610 600 L640 600 Q770 300 590 0 Z" fill="var(--swoosh)"/>
      <path class="lawn-panel" d="M590 0 Q770 300 640 600 L1050 600 L1050 0 Z" fill="url(#lawnFill)"/>
    </svg>

    <div class="brand-block">
      <div class="brand-row">
        <span class="brand-dot"></span>
        <h1 class="brand-name">Brindle Yard Care</h1>
      </div>
      <p class="tagline">I am your lawns best friend</p>
    </div>

    <div class="contact-block">
      <h2 class="contact-name">Derek</h2>
      <p class="contact-company">Brindle Yard care</p>
      <p class="contact-line">
        <svg class="contact-icon" viewBox="0 0 26 26" aria-hidden="true">
          <rect width="26" height="26" rx="3" fill="#1b1b1b"/>
          <path d="M8 6 L11 6 L12 10 L10 11.5 Q12 15 14.5 16 L16 14 L20 15 L20 18 Q13 19.5 7 9 Z" fill="#b9dc5a"/>
        </svg>
        555-812-4473
      </p>
      <p class="contact-line">
        <svg class="contact-icon" viewBox="0 0 26 26" aria-hidden="true">
          <rect width="26" height="26" rx="3" fill="#1b1b1b"/>
          <rect x="5" y="8" width="16" height="11" fill="none" stroke="#b9dc5a" stroke-width="1.8"/>
          <path d="M5 8 L13 14 L21 8" fill="none" stroke="#b9dc5a" stroke-width="1.8"/>
        </svg>
        tomvale48@quillmail.net
      </p>
      <p class="promise">100% satisfaction guarantee</p>
      <p class="promise">Fast, Friendly, quality service</p>
      <p class="services">Mowing, trimming, edging &amp; clean up<br>Free estimates</p>
    </div>
  </section>
</main>
</body>
</html>
```